Business Card Design

We need a business card designed for our new company. Prefer a black card with white logo & writing.

Contact Information for Business Card

Ted Galloway, address: 7-4812 Fernhollow Road, Abbotsford, BC, V3K 8R2, Office Phone: 604-712-3390, Cell: 604-947-2164, Email: ted@resinworkshub.ca

Colors

Designer to choose only greyscale colors for use in the design.

```html
<!DOCTYPE html>
<html lang="en">
<head>
<meta charset="utf-8">
<title>Resinworks Hub – Business Card</title>
<link href="https://fonts.googleapis.com/css2?family=Montserrat:wght@400;700;800&display=swap" rel="stylesheet">
<style>
  :root {
    --stage: #1e1e1e;
    --card: #2b2b2b;
    --ink: #ffffff;
    --ink-soft: #d9d9d9;
    --ridge-light: #4a4a4a;
    --ridge-dark: #2b2b2b;
  }
  * { box-sizing: border-box; margin: 0; padding: 0; }
  html, body {
    width: 1200px; height: 1200px; overflow: hidden;
    background: var(--stage);
    font-family: "Montserrat", sans-serif;
    color: var(--ink);
  }
  .stage {
    position: relative; width: 1200px; height: 1200px;
  }
  .card {
    position: absolute; left: 120px; width: 960px; height: 549px;
    background: var(--card);
    box-shadow: 0 18px 40px rgba(0,0,0,0.55);
  }
  .card--contact { top: 40px; }
  .card--brand { top: 611px; display: flex; align-items: center; justify-content: center; }

  .wordmark {
    font-weight: 800; letter-spacing: 0.02em; text-transform: uppercase; color: var(--ink);
  }
  .card--contact .wordmark {
    position: absolute; left: 64px; top: 62px; font-size: 30px;
  }
  .card--brand .wordmark { font-size: 74px; }

  .person { position: absolute; left: 64px; top: 150px; }
  .person__name { font-weight: 700; font-size: 34px; line-height: 1.1; }
  .person__role { font-weight: 400; font-size: 19px; color: var(--ink-soft); margin-top: 4px; }

  .address {
    position: absolute; left: 64px; top: 240px;
    font-size: 20px; line-height: 1.3; color: var(--ink-soft); font-style: normal;
  }
  .contact-list {
    position: absolute; left: 64px; top: 318px; list-style: none;
  }
  .contact-list li {
    display: flex; align-items: center; gap: 16px;
    font-size: 20px; line-height: 37px; color: var(--ink-soft);
  }
  .contact-list svg { width: 20px; height: 20px; flex: none; }

  .ridge {
    position: absolute; right: 0; bottom: 60px; width: 600px; height: 170px;
    background: linear-gradient(160deg, var(--ridge-dark) 10%, var(--ridge-light) 60%, var(--ridge-dark) 100%);
  }
</style>
</head>
<body>
<div class="stage">

  <section class="card card--contact">
    <div class="wordmark">Resinworks Hub</div>

    <div class="person">
      <div class="person__name">Ted Galloway</div>
      <div class="person__role">owner</div>
    </div>

    <address class="address">7-4812 Fernhollow Road,<br>Abbotsford, BC, V3K 8R2</address>

    <ul class="contact-list">
      <li>
        <svg viewBox="0 0 24 24" fill="var(--ink)"><path d="M6.6 10.8a15.1 15.1 0 0 0 6.6 6.6l2.2-2.2a1 1 0 0 1 1-.25 11.4 11.4 0 0 0 3.6.57 1 1 0 0 1 1 1V20a1 1 0 0 1-1 1A17 17 0 0 1 3 4a1 1 0 0 1 1-1h3.5a1 1 0 0 1 1 1c0 1.25.2 2.45.57 3.57a1 1 0 0 1-.25 1z"/></svg>
        604-712-3390
      </li>
      <li>
        <svg viewBox="0 0 24 24" fill="none" stroke="var(--ink)" stroke-width="2"><rect x="6" y="2" width="12" height="20" rx="2"/><line x1="11" y1="18" x2="13" y2="18"/></svg>
        604-947-2164
      </li>
      <li>
        <svg viewBox="0 0 24 24" fill="var(--ink)"><path d="M2 5h20v14H2z" opacity="0"/><path d="M2 6l10 7 10-7v12H2z"/><path d="M2 5h20l-10 7z"/></svg>
        ted@resinworkshub.ca
      </li>
      <li>
        <svg viewBox="0 0 24 24" fill="none" stroke="var(--ink)" stroke-width="2"><circle cx="12" cy="12" r="9"/><path d="M3 12h18M12 3c3 3.5 3 14.5 0 18M12 3c-3 3.5-3 14.5 0 18"/></svg>
        www.resinworkshub.ca
      </li>
    </ul>

    <div class="ridge" role="img" aria-label="White line illustration of a mountain ridge sweeping across the lower right of the card"></div>
  </section>

  <section class="card card--brand">
    <div class="wordmark">Resinworks Hub</div>
  </section>

</div>
</body>
</html>
```